Water ATM Card

Need a design for water ATM cards. Size of card is 3.375 x 2.125 inch
On the Front include the Cedar hollow Logo.
Bottom right corner should have Price $100
On the Back
This card is to be used to access water refills at any Cedar Hollow Water Vending Machines.
Please contact (869) 418 2930 or (869) 534 1276 or email clearflowbox@mailvista.example for any assistance or recharging of card.

```html
<!DOCTYPE html>
<html lang="en">
<head>
<meta charset="utf-8">
<title>Cedar Hollow Water Cards</title>
<link rel="stylesheet" href="https://fonts.googleapis.com/css2?family=Montserrat:wght@700&family=Antonio:wght@100&display=swap">
<style>
  :root {
    --page-bg: #e9e7e4;
    --card-bg: #161616;
    --brand-blue: #0b72bd;
    --emboss-grey: #3b3b3b;
    --price-green: #3aa845;
  }
  html, body {
    margin: 0;
    padding: 0;
    width: 1200px;
    height: 711px;
    overflow: hidden;
    background: var(--page-bg);
  }
  .canvas {
    position: relative;
    width: 1200px;
    height: 711px;
  }
  .water-card {
    position: absolute;
    top: 185px;
    width: 540px;
    height: 340px;
    border-radius: 26px;
    background: var(--card-bg);
    overflow: hidden;
  }
  .water-card--plain { left: 40px; }
  .water-card--priced { left: 620px; }
  .brand {
    position: absolute;
    left: 0;
    right: 0;
    top: 118px;
    display: flex;
    align-items: center;
    justify-content: center;
    gap: 14px;
  }
  .brand-dot {
    width: 28px;
    height: 28px;
    border-radius: 50%;
  }
  .brand-name {
    font-family: "Montserrat", sans-serif;
    font-weight: 700;
    font-size: 38px;
    line-height: 1;
    letter-spacing: 1px;
    text-transform: uppercase;
    margin: 0;
  }
  .water-card--plain .brand-dot { background: var(--emboss-grey); }
  .water-card--plain .brand-name { color: var(--emboss-grey); }
  .water-card--priced .brand-dot { background: var(--brand-blue); }
  .water-card--priced .brand-name { color: var(--brand-blue); }
  .price-tag {
    position: absolute;
    right: 34px;
    bottom: 30px;
    font-family: "Antonio", sans-serif;
    font-weight: 100;
    font-size: 42px;
    line-height: 1;
    letter-spacing: 1px;
    color: var(--price-green);
    margin: 0;
  }
</style>
</head>
<body>
  <main class="canvas">
    <section class="water-card water-card--plain" aria-label="Cedar Hollow water card, embossed side">
      <div class="brand">
        <span class="brand-dot" aria-hidden="true"></span>
        <p class="brand-name">Cedar Hollow</p>
      </div>
    </section>
    <section class="water-card water-card--priced" aria-label="Cedar Hollow water card, price side">
      <div class="brand">
        <span class="brand-dot" aria-hidden="true"></span>
        <h1 class="brand-name">Cedar Hollow</h1>
      </div>
      <p class="price-tag">PRICE $100</p>
    </section>
  </main>
</body>
</html>
```